Design for a 4 screens iOS and Android app - "VelaTrakko"

The app allows you to track your car gasoline refill ...
We need a design for the 4 screens of the app:
a) 1 form with 3 fields.
b) 1 simple list view
c) 1 summary view
d) 1 text page
2 "alerts" items are also to be designed.
No specific guidelines, nor logo or whatever.
It will be a free app distributed on iOS and Androïd.
We just want to make it looking nice & very usable for end users.
Target Market(s)
B2C app
Industry/Entity Type
Android

```html
<!DOCTYPE html>
<html lang="en">
<head>
<meta charset="utf-8">
<title>VelaTrakko – Add refill</title>
<link rel="stylesheet" href="https://fonts.googleapis.com/css2?family=Roboto:wght@400;500;700;900&display=swap">
<style>
  :root {
    --nav-blue: #0088ff;
    --nav-divider: #cfe6ff;
    --bg-top: #7bbfe9;
    --bg-mid: #7bbfe9;
    --bg-bottom: #2469bb;
    --field-bg: #ffffff;
    --placeholder: #a5a5a5;
    --error: #f0664a;
    --button-blue: #0088ff;
    --white: #ffffff;
  }
  * { box-sizing: border-box; margin: 0; padding: 0; }
  html, body { width: 675px; height: 1200px; overflow: hidden; }
  body {
    font-family: "Roboto", Arial, sans-serif;
    background: linear-gradient(to bottom, var(--bg-top) 0%, var(--bg-mid) 58%, var(--bg-bottom) 100%);
    position: relative;
  }
  .tab-bar {
    position: absolute; top: 0; left: 0; width: 675px; height: 107px;
    background: var(--nav-blue);
    display: flex;
  }
  .tab {
    flex: 1; display: flex; align-items: center; justify-content: center;
    border-right: 1px solid var(--nav-divider);
  }
  .tab:last-child { border-right: none; }
  .refill-form {
    position: absolute; top: 363px; left: 85px; width: 505px;
  }
  .field {
    height: 81px; background: var(--field-bg); border-radius: 22px;
    display: flex; align-items: center; justify-content: space-between;
    padding: 0 44px 0 50px;
    font-size: 34px;
  }
  .field-amount { color: var(--placeholder); font-weight: 500; }
  .field-invalid {
    color: var(--error); font-weight: 500;
    width: 501px; margin-left: 2px; height: 80px;
  }
  .field-amount + .field-invalid { margin-top: 39px; }
  .field-invalid + .field-invalid { margin-top: 34px; }
  .save-button {
    position: absolute; top: 791px; left: 197px; width: 282px; height: 85px;
    background: var(--button-blue); border-radius: 20px;
    color: var(--white); font-weight: 900; font-size: 35px;
    display: flex; align-items: center; justify-content: center;
    border: none;
  }
  .about-link {
    position: absolute; top: 1062px; left: 0; width: 675px; text-align: center;
    color: var(--white); font-size: 28px; font-weight: 500;
  }
</style>
</head>
<body>
  <nav class="tab-bar" aria-label="VelaTrakko navigation">
    <div class="tab" aria-label="Add refill">
      <svg width="46" height="46" viewBox="0 0 46 46"><path d="M23 2v42M2 23h42" stroke="#fff" stroke-width="4" stroke-linecap="round"/></svg>
    </div>
    <div class="tab" aria-label="Refill list">
      <svg width="62" height="44" viewBox="0 0 62 44"><g fill="#fff"><circle cx="5" cy="4" r="4"/><circle cx="5" cy="22" r="4"/><circle cx="5" cy="40" r="4"/></g><g stroke="#fff" stroke-width="4" stroke-linecap="round"><path d="M19 4h40M19 22h40M19 40h40"/></g></svg>
    </div>
    <div class="tab" aria-label="Summary">
      <svg width="58" height="46" viewBox="0 0 58 46"><path d="M2 2v41h54" fill="none" stroke="#fff" stroke-width="4" stroke-linecap="round"/><path d="M9 37V20l6-6 8 6 8-4 8 10 8 6v5z" fill="#fff"/></svg>
    </div>
  </nav>

  <form class="refill-form">
    <div class="field field-amount">127500</div>
    <div class="field field-invalid">xyz
      <svg width="34" height="34" viewBox="0 0 34 34" aria-label="Clear"><circle cx="17" cy="17" r="15" fill="none" stroke="#f0664a" stroke-width="2.2"/><path d="M11.5 11.5l11 11M22.5 11.5l-11 11" stroke="#f0664a" stroke-width="2.2" stroke-linecap="round"/></svg>
    </div>
    <div class="field field-invalid">xyz
      <svg width="34" height="34" viewBox="0 0 34 34" aria-label="Clear"><circle cx="17" cy="17" r="15" fill="none" stroke="#f0664a" stroke-width="2.2"/><path d="M11.5 11.5l11 11M22.5 11.5l-11 11" stroke="#f0664a" stroke-width="2.2" stroke-linecap="round"/></svg>
    </div>
  </form>

  <button class="save-button" type="button">Save</button>

  <div class="about-link">About us</div>
</body>
</html>
```